Occasions chocolate packaging

We are looking for 7 packaging designs for bars of chocolate.

Each design needs to be different and we’re not looking for a consistent brand or branding message across the designs. Inspiration should come from gift/occasion cards. Fun, simple, bold, vibrant colours and eye catching, i.e. not vintage or just text.

The front of the packaging should have the main message on and is free of any branding. You don’t need to design the back, just simply allow the main background colour or design pattern to continue around.

These are the different designs we are after, I’ve added in some text for each to give you some guidance but feel free to play around with the message if it suits the design better.

1) Mum
‘The best mum’, ‘Best mum in the World’, ‘Number 1 Mum’

2) Dad
‘The Best Dad’, ‘Best Dad Ever’, ‘Number 1 Dad’, ‘You’re my hero Dad’

3) Husband
‘Best Husband in the World’, ‘Husband I Love You’, ‘Darling Husband’

4) Wife
‘Best Wife in the World’, ‘For my Wonderful Wife’, ‘My Beautiful Wife’

5) Congratulations
Simple one, just Congratulations

6) Thinking of you
Try and keep this neutral as it could be used for happy and sad situations.

7) Thank you
Keep this gender neutral.

Sides:
The sides need to have the following text:

FINE BELGIAN DARK CHOCOLATE
infused with Orange

Back:
The main colour of the front should continue all the way around, we will place a box with the contents and bar code on here ourselves so no need to do anything.

Dimensions:
Attached in the document, front of package is 85mm by 190mm.

The packaging is made from folded card, the first blank part is for gluing the back on to.

Reason: I'm extending the deadline as I've only received 1 design so far which has followed the brief. Although I do like it, I would like to see at least some competition...

```html
<!DOCTYPE html>
<html lang="en">
<head>
<meta charset="utf-8">
<title>Best Mum in the World – Chocolate Bar Wrap</title>
<link rel="stylesheet" href="https://fonts.googleapis.com/css2?family=Oswald:wght@400;500;700&display=swap">
<style>
  :root {
    --backdrop: #ececee;
    --magenta: #e4177a;
    --magenta-deep: #c9106a;
    --magenta-light: #f0308b;
    --side-magenta: #d01470;
    --ink-white: #ffffff;
    --figure-white: #fbf4f8;
    --figure-pink: #f7c6dc;
  }
  * { box-sizing: border-box; margin: 0; padding: 0; }
  html, body {
    width: 1200px;
    height: 960px;
    overflow: hidden;
    background: var(--backdrop);
  }
  .wrap {
    position: absolute;
    left: 379px;
    top: 50px;
    width: 442px;
    height: 860px;
    display: flex;
  }
  .side-panel {
    width: 56px;
    height: 100%;
    background: linear-gradient(180deg, var(--side-magenta), var(--magenta-deep));
    display: flex;
    align-items: center;
    justify-content: center;
  }
  .side-text {
    writing-mode: vertical-rl;
    transform: rotate(180deg);
    font-family: 'Oswald', sans-serif;
    color: var(--ink-white);
    font-size: 22px;
    letter-spacing: 3px;
    white-space: nowrap;
    display: flex;
    gap: 40px;
    align-items: center;
  }
  .side-text .product { font-weight: 500; }
  .side-text .flavour { font-weight: 400; font-size: 19px; letter-spacing: 2px; }
  .front-panel {
    position: relative;
    width: 386px;
    height: 100%;
    background: radial-gradient(ellipse at 50% 40%, var(--magenta-light) 0%, var(--magenta) 55%, var(--magenta-deep) 100%);
    overflow: hidden;
  }
  .illustration {
    position: absolute;
    left: 78px;
    top: 40px;
    width: 230px;
    height: 440px;
  }
  .headline {
    position: absolute;
    left: 0;
    right: 0;
    top: 492px;
    text-align: center;
    font-family: 'Oswald', sans-serif;
    font-weight: 700;
    color: var(--ink-white);
    text-transform: uppercase;
    line-height: 0.92;
  }
  .headline .line-best { display: block; font-size: 140px; letter-spacing: -2px; }
  .headline .line-mum { display: block; font-size: 120px; letter-spacing: -2px; margin-top: 4px; }
  .headline .line-world { display: block; font-size: 52px; letter-spacing: -1.5px; margin-top: 10px; }
</style>
</head>
<body>
  <main class="wrap">
    <aside class="side-panel">
      <p class="side-text">
        <span class="product">FINE BELGIAN DARK CHOCOLATE</span>
        <span class="flavour">infused with Orange</span>
      </p>
    </aside>
    <section class="front-panel">
      <svg class="illustration" viewBox="0 0 230 440" role="img" aria-label="White silhouette illustration of a mother bending down to hand a pink heart to her little daughter">
        <defs>
          <linearGradient id="figure-fill" x1="0" y1="0" x2="0" y2="1">
            <stop offset="0" stop-color="var(--figure-white)" stop-opacity="0.55"/>
            <stop offset="1" stop-color="var(--figure-pink)" stop-opacity="0.3"/>
          </linearGradient>
        </defs>
        <rect x="0" y="0" width="230" height="440" rx="60" fill="url(#figure-fill)"/>
      </svg>
      <h1 class="headline">
        <span class="line-best">Best</span>
        <span class="line-mum">Mum</span>
        <span class="line-world">In the World</span>
      </h1>
    </section>
  </main>
</body>
</html>
```